Take Sunward Path Now Road Tour

I need a Chatterbox cover photo design for my holisitic health and wellness campaign "Take Sunward Path Now."

-Purpose: Quest to find a healthier me through career, relationships and food
-Documentary (Similar to the documentary "Tired Stuck and Barely Well")- interviewing professionals along the way in the field I work in, the entertainment industry, on health and wellness as it relates to career, relationships and food. We will also capture footage from my mom, phone calls from friends, pre planning, meditation, me working while on the road, farmers market trips, healthy restaurants, music venues and plays.
-Cities and States we will visit: Lincoln, Nebraska; Denver, Colorado; Las Vegas, Nevada; Studio City, California
Timeline and Distance: Over 2000 miles, over 31 hours, over the course of 5 days (Sept 12th-16th.
-Interesting fact #1: I sold everything, even my car and I'm relocating to California for this quest for a healthier happier me.
-Interesting fact #2: My mom from Maryland is flying in this friday to support me and drive as well.
-Interesting fact #3: I am currently in nutrition school to be a certified health coach
-We are encouraging our Chatterbox fans to follow us on our chatterbox pages as well. -Donations: Followers can also donate to the campaign on our fundwell page. All proceeds will go to me starting a business in helping professionals in my industry live longer healthier lives through career, relationships and food.

WHAT I"M LOOKING FOR
I would like to see designs that are fun. The design when seen by viewers on Chatterbox should tell a story of me on a quest for a healthier me, selling everything I own, hopping in a car and driving through the various cities to find my truest self. The final design should communicate a road being taken to the healthier happier me through career, relationships and food.
Updates

The name of the campaign is "Take Sunward Path Now" Also the campaign to raise funds for those interested will be posted on my website, once the creative is completed at www.KTRholdings.example. Thank you all! I am looking forward to seeing your work! Marisol T.

Update to cities and states 1) Lincoln, Nebraska 2) Denver, Colorado 3) Albuquerque, New Mexico 4) Las Vegas, Nevada 5) Studio City, California

Target Market(s)

Entertainment Professionals who eventually will want me to coach them in their careers, relationships and with food.

Industry/Entity Type

Entertainment

```html
<!DOCTYPE html>
<html lang="en">
<head>
<meta charset="utf-8">
<title>Take Sunward Path Now – Road Tour Cover</title>
<link href="https://fonts.googleapis.com/css2?family=Anton&family=Roboto+Condensed:ital,wght@0,400;0,700;1,700&display=swap" rel="stylesheet">
<style>
  :root {
    --orange-deep: #f0601a;
    --orange-mid: #f39a3c;
    --sun-pale: #e6df8e;
    --road-dark: #2b2624;
    --road-stripe: #f26a1b;
    --ink: #1d1a19;
    --title-fill: #ffffff;
    --landmark-grey: #8d8b88;
    --landmark-light: #c9c6c1;
    --car-red: #d7262b;
  }
  html, body {
    margin: 0;
    padding: 0;
    width: 1200px;
    height: 444px;
    overflow: hidden;
    background: #ffffff;
  }
  .cover {
    position: relative;
    width: 1200px;
    height: 444px;
    overflow: hidden;
    background: linear-gradient(90deg, var(--orange-deep) 0%, var(--orange-deep) 22%, var(--orange-mid) 55%, var(--sun-pale) 100%);
    font-family: "Roboto Condensed", Arial, sans-serif;
    color: var(--ink);
  }
  .campaign-title {
    position: absolute;
    left: 24px;
    top: 30px;
    width: 300px;
    margin: 0;
    font-family: "Roboto Condensed", Arial, sans-serif;
    font-weight: 700;
    font-size: 50px;
    line-height: 1.05;
    color: var(--title-fill);
  }
  .headline {
    position: absolute;
    left: 420px;
    top: 26px;
    margin: 0;
    font-family: "Anton", Impact, sans-serif;
    font-weight: 400;
    font-size: 40px;
    letter-spacing: 0.5px;
    color: var(--ink);
    transform: skewX(-10deg);
    white-space: nowrap;
  }
  .tour-dates {
    position: absolute;
    right: 40px;
    top: 92px;
    margin: 0;
    font-family: "Anton", Impact, sans-serif;
    font-size: 28px;
    color: var(--ink);
    transform: skewX(-10deg);
    white-space: nowrap;
  }
  .tour-dates sup { font-size: 15px; }
  .stop {
    position: absolute;
    text-align: center;
    transform: translateX(-50%);
    font-size: 17px;
    line-height: 1.15;
    color: var(--ink);
    white-space: nowrap;
  }
  .stop .stop-date { display: block; font-weight: 700; font-size: 14px; }
  .landmark {
    position: absolute;
    background: linear-gradient(180deg, var(--landmark-light), var(--landmark-grey));
    border-radius: 4px 4px 0 0;
  }
  .car {
    position: absolute;
    left: 1075px;
    top: 315px;
    width: 110px;
    height: 52px;
    border-radius: 26px 34px 10px 10px;
    background: linear-gradient(180deg, #ef4a4e, var(--car-red));
  }
  .road {
    position: absolute;
    left: 0;
    top: 0;
    width: 1200px;
    height: 444px;
  }
  .road-line { font-family: "Roboto Condensed", Arial, sans-serif; font-style: italic; font-weight: 700; fill: var(--road-stripe); }
  .road-motto { font-size: 20px; letter-spacing: 0.6px; }
  .road-story { font-size: 19px; letter-spacing: 0.5px; }
</style>
</head>
<body>
<main class="cover">
  <h1 class="campaign-title">Take Sunward Path Now</h1>

  <p class="headline">MOM AND DAUGHTER, 4 DAYS, OVER 2000 MILES</p>
  <p class="tour-dates">SEP 12<sup>TH</sup> - 16<sup>TH</sup> ON ROADS...</p>

  <div class="stop" style="left:323px; top:222px;">Studio City<br>California<span class="stop-date">(16 Sept)</span></div>
  <div class="stop" style="left:441px; top:206px;">Las Vegas<br>Nevada<span class="stop-date">(15 Sept)</span></div>
  <div class="stop" style="left:617px; top:192px;">Albuquerque<br>New Mexico<span class="stop-date">(14 Sept)</span></div>
  <div class="stop" style="left:750px; top:206px;">Denver<br>Colorado<span class="stop-date">(13 Sept)</span></div>
  <div class="stop" style="left:893px; top:172px;">Lincoln<br>Nebraska<span class="stop-date">(12 Sept)</span></div>
  <div class="stop" style="left:1070px; top:183px;">Starting from<br>Chicago, IL</div>

  <svg class="road" viewBox="0 0 1200 444">
    <defs>
      <path id="motto-curve" d="M352,432 Q720,330 1190,382"/>
    </defs>
    <path d="M254,444 L268,406 Q640,318 1200,328 L1200,444 Z" fill="var(--road-dark)"/>
    <text class="road-line road-motto">
      <textPath href="#motto-curve" startOffset="0">A road to the healthier happier me through career, relationships and food</textPath>
    </text>
    <text class="road-line road-story" x="800" y="404" text-anchor="middle">Selling everything, hopping in a car</text>
    <text class="road-line road-story" x="800" y="430" text-anchor="middle">driving through the various cities to find truest self</text>
  </svg>

  <div class="landmark" role="img" aria-label="Studio City welcome sign" style="left:268px; top:303px; width:110px; height:78px;"></div>
  <div class="landmark" role="img" aria-label="Las Vegas welcome sign with palm trees" style="left:395px; top:275px; width:92px; height:84px;"></div>
  <div class="landmark" role="img" aria-label="Albuquerque adobe church landmark" style="left:543px; top:256px; width:148px; height:84px;"></div>
  <div class="landmark" role="img" aria-label="Denver painted cow statue" style="left:712px; top:270px; width:99px; height:62px;"></div>
  <div class="landmark" role="img" aria-label="Nebraska State Capitol building" style="left:832px; top:234px; width:127px; height:90px;"></div>
  <div class="landmark" role="img" aria-label="Chicago skyline and Cloud Gate sculpture" style="left:987px; top:247px; width:141px; height:82px;"></div>
  <div class="car" role="img" aria-label="Red car driving on the road"></div>
</main>
</body>
</html>
```